Tolbek cards

I want a simple business card that pops.
Logo on one side.
On side two i want.
"Are you thinking about a new building on your property, or renovating an existing structure? Contact".....
Owners Name: Dale Whitacre
Owners Phone number: 610-555-0187
Address:4076 Copper Ridge RD, Alderton, NY 13409
Committed to Quality, Service, and Integrity

```html
<!DOCTYPE html>
<html lang="en">
<head>
<meta charset="utf-8">
<title>Tolbek Builders – Business Card</title>
<link rel="stylesheet" href="https://fonts.googleapis.com/css2?family=Bebas+Neue&family=Montserrat:wght@600;700&family=Poppins:wght@400&display=swap">
<style>
  :root {
    --page-bg: #2a2a2a;
    --card-bg: #0e0d0c;
    --card-edge: #b39676;
    --gold: #a8845f;
    --gold-line: #6e5a45;
    --white: #f4f2ef;
  }
  html, body {
    margin: 0;
    width: 1200px;
    height: 900px;
    overflow: hidden;
    background: var(--page-bg);
  }
  .sheet {
    width: 1200px;
    height: 900px;
    display: flex;
    flex-direction: column;
    align-items: center;
    justify-content: center;
    gap: 48px;
  }
  .card {
    position: relative;
    width: 650px;
    height: 372px;
    background: var(--card-bg);
    border-radius: 22px;
    box-shadow: 0 3px 0 var(--card-edge);
    overflow: hidden;
  }

  /* Logo side */
  .card--logo {
    display: flex;
    align-items: center;
    justify-content: center;
  }
  .brand {
    display: flex;
    align-items: center;
    gap: 18px;
  }
  .brand__square {
    width: 54px;
    height: 54px;
    background: var(--gold);
  }
  .brand__text {
    display: flex;
    flex-direction: column;
  }
  .brand__name {
    font-family: "Montserrat", sans-serif;
    font-weight: 700;
    font-size: 64px;
    line-height: 1;
    letter-spacing: 2px;
    color: var(--gold);
    text-transform: uppercase;
  }
  .brand__tagline {
    font-family: "Montserrat", sans-serif;
    font-weight: 600;
    font-size: 19px;
    letter-spacing: 3px;
    color: var(--gold);
    text-transform: uppercase;
    margin-top: 4px;
    margin-left: 24px;
  }

  /* Contact side */
  .rule {
    position: absolute;
    height: 1px;
    background: var(--gold-line);
  }
  .rule--top { left: 28px; right: 40px; top: 40px; }
  .rule--mid { left: 28px; right: 40px; top: 122px; }
  .rule--low { left: 48px; width: 300px; top: 188px; }
  .headline {
    position: absolute;
    left: 28px;
    right: 40px;
    top: 48px;
    margin: 0;
    font-family: "Bebas Neue", sans-serif;
    font-weight: 400;
    font-size: 30px;
    line-height: 1.08;
    color: var(--white);
    text-align: center;
    letter-spacing: 0.3px;
  }
  .mark {
    position: absolute;
    right: 46px;
    top: 160px;
    font-family: "Montserrat", sans-serif;
    font-weight: 700;
    font-size: 52px;
    letter-spacing: 2px;
    color: var(--gold);
    text-transform: uppercase;
  }
  .contact {
    position: absolute;
    left: 52px;
    bottom: 34px;
    font-family: "Poppins", sans-serif;
    color: var(--white);
  }
  .contact__label {
    font-size: 17px;
    margin: 0;
  }
  .contact__name {
    font-family: "Montserrat", sans-serif;
    font-weight: 600;
    font-size: 25px;
    letter-spacing: 1px;
    color: var(--gold);
    text-transform: uppercase;
    margin: 0 0 6px;
  }
  .contact__row {
    display: flex;
    align-items: flex-start;
    gap: 12px;
    font-size: 17px;
    line-height: 1.3;
    margin-top: 6px;
  }
  .contact__icon {
    flex: none;
    width: 20px;
    height: 20px;
    margin-top: 1px;
  }
</style>
</head>
<body>
<main class="sheet">

  <section class="card card--logo" aria-label="Card front">
    <div class="brand">
      <span class="brand__square" aria-hidden="true"></span>
      <div class="brand__text">
        <span class="brand__name">Tolbek</span>
        <span class="brand__tagline">Builders LLC</span>
      </div>
    </div>
  </section>

  <section class="card card--contact" aria-label="Card back">
    <span class="rule rule--top"></span>
    <h1 class="headline">Are you thinking about a new building on your property,<br>or renovating an existing structure?</h1>
    <span class="rule rule--mid"></span>
    <span class="rule rule--low"></span>

    <div class="mark">Tolbek</div>

    <div class="contact">
      <p class="contact__label">Contact</p>
      <p class="contact__name">Dale Whitacre</p>
      <div class="contact__row">
        <svg class="contact__icon" viewBox="0 0 20 20" aria-hidden="true">
          <circle cx="10" cy="10" r="10" fill="#f4f2ef"/>
          <path d="M7 5.5l1.6 2.2-1 1.1a6 6 0 0 0 3.6 3.6l1.1-1 2.2 1.6-.8 1.6c-3.8.2-7.5-3.5-7.3-7.3z" fill="#0e0d0c"/>
        </svg>
        <span>610-555-0187</span>
      </div>
      <div class="contact__row">
        <svg class="contact__icon" viewBox="0 0 20 20" aria-hidden="true">
          <circle cx="10" cy="10" r="10" fill="#f4f2ef"/>
          <path d="M10 4.5a3.6 3.6 0 0 0-3.6 3.6c0 2.7 3.6 7 3.6 7s3.6-4.3 3.6-7A3.6 3.6 0 0 0 10 4.5zm0 5a1.4 1.4 0 1 1 0-2.8 1.4 1.4 0 0 1 0 2.8z" fill="#0e0d0c"/>
        </svg>
        <span>4076 Copper Ridge RD,<br>Alderton, NY 13409</span>
      </div>
    </div>
  </section>

</main>
</body>
</html>
```